Bookcover: Ways to Turn Into a Bold Pathfinder

I am publishing a super-low-cost innovation book for €4,99 on Quillmere Open Press to help everyone become a great innovator: young ambitious people without college education nor a big budget. Do you want to help me?

Brief:
Design a book cover 1600 x 2560 pixels for QOP.
Main title: Ways to Turn Into a Bold Pathfinder
Sub title: mindset - insights - skills & tools
Author: Joost ter Brakel
Design: captive, and appealing to everyone
Target Group: young ambitious people without college education

For quillmere please format the height/width ratio of 1.6:1

```html
<!DOCTYPE html>
<html lang="en">
<head>
<meta charset="utf-8">
<title>Ways to Turn Into a Bold Pathfinder – Cover Models</title>
<link href="https://fonts.googleapis.com/css2?family=Lato:wght@300;700;900&family=Roboto:ital,wght@1,300&display=swap" rel="stylesheet">
<style>
  :root {
    --page-bg: #ffffff;
    --label-ink: #111111;
    --orange-a: #f9844a;
    --orange-b: #fdb45a;
    --yellow-a: #fbe58a;
    --yellow-b: #fcd95a;
    --brown-ink: #3d1a0c;
    --white-ink: #ffffff;
    --black-ink: #111111;
    --art-warm: #e8693f;
  }
  * { box-sizing: border-box; margin: 0; padding: 0; }
  html, body { width: 1200px; height: 1200px; overflow: hidden; background: var(--page-bg); }
  .sheet {
    position: relative; width: 1200px; height: 1200px;
    display: flex; justify-content: center; align-items: center; gap: 25px;
  }
  .model { width: 350px; display: flex; flex-direction: column; align-items: center; }
  .model-label {
    font-family: "Lato", sans-serif; font-weight: 300; font-size: 58px;
    color: var(--label-ink); line-height: 1; margin-bottom: 38px;
  }
  .cover {
    position: relative; width: 350px; height: 560px; overflow: hidden;
    text-align: center; font-family: "Lato", sans-serif;
  }
  .cover--orange { background: radial-gradient(ellipse at 65% 50%, var(--orange-b) 0%, var(--orange-a) 75%); }
  .cover--yellow { background: linear-gradient(135deg, var(--yellow-a) 0%, var(--yellow-b) 55%, var(--yellow-a) 100%); }
  .cover--dark  { color: var(--brown-ink); }
  .cover--light { color: var(--white-ink); text-shadow: 0 1px 2px rgba(90,40,10,.55); }
  .cover--black { color: var(--black-ink); }

  .kicker { position: absolute; top: 50px; left: 0; right: 0; font-weight: 300; font-size: 20px; letter-spacing: .2px; }
  .title-line { position: absolute; left: 0; right: 0; font-weight: 900; line-height: 1; }
  .title-line--one { top: 78px; font-size: 54px; letter-spacing: 4px; }
  .title-line--two { top: 134px; font-size: 43px; letter-spacing: -.5px; }
  .subtitle { position: absolute; top: 190px; left: 0; right: 0; font-weight: 700; font-size: 15px; }

  .artwork {
    position: absolute; top: 228px; left: 22px; width: 306px; height: 252px;
    border-radius: 50% 50% 8px 8px / 60% 60% 8px 8px;
    background: radial-gradient(circle at 50% 45%, rgba(255,255,255,.75) 0%, rgba(255,255,255,.35) 40%, rgba(232,105,63,.35) 75%, rgba(232,105,63,0) 100%);
  }
  .baseline { position: absolute; top: 485px; left: 80px; width: 220px; height: 2px; background: var(--white-ink); }
  .author {
    position: absolute; top: 503px; left: 0; right: 0;
    font-family: "Roboto", sans-serif; font-style: italic; font-weight: 300; font-size: 22px;
  }
</style>
</head>
<body>
<main class="sheet">
  <section class="model">
    <h2 class="model-label">Model 01</h2>
    <article class="cover cover--orange cover--dark">
      <p class="kicker">WAYS TO TURN INTO</p>
      <h1 class="title-line title-line--one">A BOLD</h1>
      <h1 class="title-line title-line--two">PATHFINDER</h1>
      <p class="subtitle">Mindset - Insights - Skills &amp; Tools</p>
      <div class="artwork" role="img" aria-label="Illustration of a head silhouette with a light bulb and gears, surrounded by icons for a clock, clipboard, target and rising chart above a conveyor belt"></div>
      <div class="baseline"></div>
      <p class="author">Joost ter Brakel</p>
    </article>
  </section>

  <section class="model">
    <h2 class="model-label">Model 02</h2>
    <article class="cover cover--orange cover--light">
      <p class="kicker">WAYS TO TURN INTO</p>
      <h1 class="title-line title-line--one">A BOLD</h1>
      <h1 class="title-line title-line--two">PATHFINDER</h1>
      <p class="subtitle">Mindset - Insights - Skills &amp; Tools</p>
      <div class="artwork" role="img" aria-label="Illustration of a head silhouette with a light bulb and gears, surrounded by icons for a clock, clipboard, target and rising chart above a conveyor belt"></div>
      <div class="baseline"></div>
      <p class="author">Joost ter Brakel</p>
    </article>
  </section>

  <section class="model">
    <h2 class="model-label">Model 03</h2>
    <article class="cover cover--yellow cover--black">
      <p class="kicker">WAYS TO TURN INTO</p>
      <h1 class="title-line title-line--one">A BOLD</h1>
      <h1 class="title-line title-line--two">PATHFINDER</h1>
      <p class="subtitle">Mindset - Insights - Skills &amp; Tools</p>
      <div class="artwork" role="img" aria-label="Illustration of a head silhouette with a light bulb and gears, surrounded by icons for a clock, clipboard, target and rising chart above a conveyor belt"></div>
      <div class="baseline"></div>
      <p class="author">Joost ter Brakel</p>
    </article>
  </section>
</main>
</body>
</html>
```